Bluefinch Painting needs a Website

We need a website built for a Painting company I own, we mainly do residential painting, but don't want to be limited to that.

Need to have estimate request form.
Need pic's of past projects

I like the look of the website for http://www.harbor-brushworks.com
& "Westlake Home inspections"

My logo that was designed here on ArtHatch on the front page

I would like one of the houses I downloaded as part of the background
of the front page.

Target Market(s)

Home owners

Industry/Entity Type

Painting

Number of Pages Required

1 page

Font styles to use
Serif

Requirements
Must have
• Estimate request form for home owners to fill out -
• Name:
• Phone Number:
• Address:
• E-mail:
• Painting project description:
• And my info to:
• My phone number: (555) 318-7046
• My web address bluefinchpainting.example
Nice to have
• My logo that was designed here on ArtHatch

```html
<!DOCTYPE html>
<html lang="en">
<head>
<meta charset="utf-8">
<title>Bluefinch Painting</title>
<link href="https://fonts.googleapis.com/css2?family=Tinos:wght@400;700&display=swap" rel="stylesheet">
<style>
:root{
  --blue:#1a6aa9;
  --blue-dark:#0f5a96;
  --link:#2179bd;
  --ink:#1d1d1d;
  --muted:#9a9a9a;
  --field:#efefef;
  --panel:#eeeeee;
  --white:#ffffff;
}
*{margin:0;padding:0;box-sizing:border-box}
html,body{width:830px;height:1200px;overflow:hidden;background:var(--white)}
body{font-family:"Tinos","Times New Roman",serif;color:var(--ink);position:relative}
.abs{position:absolute}

/* header */
.site-header{left:0;top:0;width:830px;height:70px;background:var(--white);box-shadow:0 1px 3px rgba(0,0,0,.12);z-index:2}
.brand{display:flex;align-items:center;gap:8px}
.brand-mark{width:22px;height:22px;background:var(--blue)}
.brand-name{font-size:22px;letter-spacing:1.5px;color:var(--ink);text-transform:uppercase;line-height:1}
.site-header .brand{left:60px;top:22px}
.header-phone{right:26px;top:14px;font-size:20px;color:var(--ink);display:flex;align-items:center;gap:6px}
.main-nav{right:26px;top:44px;display:flex;gap:32px;font-size:10px;text-transform:uppercase;align-items:center}
.main-nav .active{color:var(--link);font-weight:700}

/* hero */
.hero{left:0;top:70px;width:830px;height:279px;background:linear-gradient(180deg,#8fb6e2 0%,#b7cfe9 30%,#a3927b 55%,#6e6454 80%,#3f4a32 100%)}
.hero-tag{left:62px;top:279px;width:363px;height:70px;background:rgba(26,106,169,.85);color:var(--white);padding:14px 0 0 16px;font-size:18px;letter-spacing:2.5px;line-height:22px;font-weight:700}
.hero-note{left:428px;top:279px;width:402px;height:70px;background:rgba(20,30,25,.78);color:var(--white);padding:19px 0 0 20px;font-size:12px;line-height:15px}
.hero-note a{color:#4aa3e6;font-weight:700;text-decoration:underline}
.hero-menu{right:24px;top:300px}

/* estimate form */
.section-title{font-size:19px;text-transform:uppercase;font-weight:400}
.estimate-title{left:76px;top:388px}
.send-btn{right:76px;top:392px;font-size:11px;font-weight:700;border-bottom:1px solid var(--blue);padding:0 6px 2px;display:flex;align-items:center;gap:6px}
.rule{left:76px;top:418px;width:678px;height:1px;background:#e4e4e4}
.field{background:var(--field);font-family:Arial,sans-serif;font-size:8px;color:var(--muted);padding:11px 0 0 15px;text-transform:uppercase;border-bottom:2px solid #e2e2e2}
.field-name{left:76px;top:427px;width:296px;height:29px}
.field-phone{left:76px;top:461px;width:296px;height:29px}
.field-address{left:76px;top:494px;width:296px;height:29px}
.field-email{left:76px;top:528px;width:296px;height:29px}
.field-desc{left:377px;top:427px;width:377px;height:130px}

/* welcome */
.welcome-band{left:0;top:606px;width:830px;height:266px;background:var(--blue)}
.welcome{left:77px;top:644px;width:441px;color:var(--white)}
.welcome h2{font-size:19px;letter-spacing:2.5px;text-transform:uppercase;padding-bottom:8px;border-bottom:1px solid rgba(255,255,255,.35);margin-bottom:12px}
.welcome h3{font-size:9.5px;font-weight:700;margin-bottom:4px}
.welcome p{font-size:9px;line-height:11.7px;margin-bottom:6px}
.quality{left:531px;top:606px;width:223px;height:266px;background:var(--white);text-align:center;padding-top:40px}
.quality h2{font-size:18px;letter-spacing:3px;color:var(--blue);line-height:22px;font-weight:700;text-transform:uppercase}
.supplier{margin-top:36px;display:flex;flex-direction:column;align-items:center;gap:12px}
.supplier-mark{width:40px;height:40px;background:#c3243c}
.supplier-name{font-size:28px;line-height:30px;color:var(--blue-dark)}

/* projects */
.projects-band{left:0;top:872px;width:830px;height:217px;background:var(--panel)}
.projects-title{left:76px;top:907px}
.carousel-nav{right:76px;top:906px;display:flex;gap:8px}
.thumb{top:948px;width:130px;height:110px}
.t1{left:76px;background:linear-gradient(180deg,#8b9993,#536b44 55%,#9a9a98)}
.t2{left:213px;background:linear-gradient(180deg,#5c7fa3,#2f4d6e 60%,#23344a)}
.t3{left:350px;background:linear-gradient(180deg,#7ea7d6,#585c60 55%,#9d9c98)}
.t4{left:486px;background:linear-gradient(180deg,#9bbde4,#a3937a 50%,#5e6b3c)}
.t5{left:623px;background:linear-gradient(180deg,#c7d7e6,#8f8370 50%,#4e6430)}
.thumb-overlay{left:213px;top:948px;width:130px;height:110px;background:rgba(16,60,110,.55);color:var(--white);font-size:9.5px;font-weight:700;text-align:right;padding:72px 8px 0 0;line-height:11px}
.zoom{left:311px;top:992px}

/* footer */
.footer-nav{left:76px;top:1119px;display:flex;gap:32px;font-size:9px;text-transform:uppercase}
.footer-nav .active{color:var(--link);font-weight:700;text-decoration:underline}
.footer-call{left:76px;top:1148px;font-size:11px;font-weight:700;display:flex;align-items:baseline;gap:7px}
.footer-call .num{font-size:18px;color:var(--link);font-weight:400}
.footer-call .more{font-weight:400}
.site-footer .brand{left:490px;top:1122px}
.copyright{left:526px;top:1160px;font-size:9.5px}
</style>
</head>
<body>

<header class="site-header abs">
  <div class="brand abs"><span class="brand-mark"></span><span class="brand-name">Bluefinch Painting</span></div>
  <div class="header-phone abs">
    <svg width="16" height="16" viewBox="0 0 24 24"><path fill="#1a6aa9" d="M6.6 10.8a15 15 0 0 0 6.6 6.6l2.2-2.2c.3-.3.7-.4 1-.2 1.1.4 2.3.6 3.6.6.6 0 1 .4 1 1V20c0 .6-.4 1-1 1A17 17 0 0 1 3 4c0-.6.4-1 1-1h3.5c.6 0 1 .4 1 1 0 1.3.2 2.5.6 3.6.1.3 0 .7-.2 1z"/></svg>
    (555) 318-7046
  </div>
  <nav class="main-nav abs">
    <span class="active">Home</span><span>About</span><span>Services</span><span>Projects</span><span>Free Quote</span>
    <svg width="10" height="10" viewBox="0 0 10 10"><circle cx="4" cy="4" r="3" fill="none" stroke="#222" stroke-width="1.2"/><line x1="6.2" y1="6.2" x2="9.2" y2="9.2" stroke="#222" stroke-width="1.2"/></svg>
  </nav>
</header>

<div class="hero abs" role="img" aria-label="Photo of a freshly painted two-storey house with flowering shrubs"></div>
<div class="hero-tag abs">EXTERIOR - INTERIOR<br>RESIDENTIAL - COMMERCIAL</div>
<div class="hero-note abs">We offer Interior and Exterior House Painting<br>throughout the USA. Get a <a>Free Quote</a></div>
<svg class="hero-menu abs" width="18" height="26" viewBox="0 0 18 26"><rect y="2" width="18" height="4" fill="#fff"/><rect y="11" width="18" height="4" fill="#fff"/><rect y="20" width="18" height="4" fill="#fff"/></svg>

<h2 class="section-title estimate-title abs">Estimate Request Form</h2>
<div class="send-btn abs">SEND REQUEST
  <svg width="14" height="8" viewBox="0 0 14 8"><path d="M0 4h11M8 1l3 3-3 3" stroke="#1a6aa9" stroke-width="1.5" fill="none"/></svg>
</div>
<div class="rule abs"></div>
<div class="field field-name abs">Name*</div>
<div class="field field-phone abs">Phone Number*</div>
<div class="field field-address abs">Address*</div>
<div class="field field-email abs">E-mail*</div>
<div class="field field-desc abs">Painting Project Description...</div>

<div class="welcome-band abs"></div>
<section class="welcome abs">
  <h2>Welcome to Bluefinch Painting</h2>
  <h3>We offer Interior and Exterior House Painting throughout the USA.</h3>
  <p>Lorem ipsum dolor sit amet, consectetuer adipiscing elit, sed diam nonummy nibh euismod tincidunt ut laoreet dolore magna aliquam erat volutpat. Ut wisi enim ad minim veniam, quis nostrud exerci tation ullamcorper suscipit lobortis nisl ut aliquip ex ea commodo consequat. Duis autem vel eum iriure dolor in hendrerit in vulputate velit esse molestie consequat, vel illum dolore eu feugiat nulla facilisis at vero eros et accumsan et iusto odio dignissim qui blandit praesent luptatum zzril delenit augue duis dolore te feugait nulla facilisi.</p>
  <p>Duis autem vel eum iriure dolor in hendrerit in vulputate velit esse molestie consequat, vel illum dolore eu feugiat nulla facilisis at vero eros et accumsan et iusto odio dignissim qui blandit praesent luptatum zzril delenit augue duis dolore te feugait nulla facilisi. Lorem ipsum dolor sit amet, consectetuer adipiscing elit, sed diam nonummy nibh euismod tincidunt ut laoreet dolore magna aliquam erat volutpat. Ut wisi enim ad minim veniam, quis nostrud exerci tation ullamcorper suscipit lobortis nisl ut aliquip ex ea commodo consequat.</p>
</section>
<aside class="quality abs">
  <h2>We Proudly Use<br>Quality</h2>
  <div class="supplier"><span class="supplier-mark"></span><span class="supplier-name">Harborline<br>Paints</span></div>
</aside>

<div class="projects-band abs"></div>
<h2 class="section-title projects-title abs">Past Projects</h2>
<svg class="carousel-nav abs" width="36" height="18" viewBox="0 0 36 18"><path d="M9 1L2 9l7 8" stroke="#bbb" stroke-width="1.2" fill="none"/><path d="M27 1l7 8-7 8" stroke="#222" stroke-width="1.2" fill="none"/></svg>
<div class="thumb t1 abs" role="img" aria-label="Project photo: house with landscaped front yard"></div>
<div class="thumb t2 abs" role="img" aria-label="Project photo: blue exterior house painting"></div>
<div class="thumb t3 abs" role="img" aria-label="Project photo: grey house with garage"></div>
<div class="thumb t4 abs" role="img" aria-label="Project photo: tan house with flowering shrubs"></div>
<div class="thumb t5 abs" role="img" aria-label="Project photo: house entrance with stone accents"></div>
<div class="thumb-overlay abs">EXTERIOR HOUSE<br>PAINTING</div>
<svg class="zoom abs" width="22" height="22" viewBox="0 0 22 22"><circle cx="9" cy="9" r="7.5" fill="none" stroke="#fff" stroke-width="1.5"/><path d="M9 5v8M5 9h8M14.5 14.5l6 6" stroke="#fff" stroke-width="1.5"/></svg>

<footer class="site-footer">
  <nav class="footer-nav abs"><span class="active">Home</span><span>About</span><span>Services</span><span>Projects</span><span>Free Quote</span></nav>
  <div class="footer-call abs">CALL FOR A FREE QUOTE: <span class="num">(555) 318-7046</span> <span>or</span> <span class="more">Click Here...</span></div>
  <div class="brand abs"><span class="brand-mark"></span><span class="brand-name">Bluefinch Painting</span></div>
  <div class="copyright abs">© 2014 Bluefinch Painting. All Rights Reserved.</div>
</footer>

</body>
</html>
```